Meadow Gate Labradoodle web design

We're a new labradoodle breeder in Charleston, SC in need of a web design.

Our name is Meadow Gate Labradoodles.

Site we like: http://www.pebblefieldlabradoodles.com/
http://www.quillbrookfarmlabradoodles.com/

Logo Font:
The ''Meadow Gate'' font is called TestarossaNF and is available freely at http://www.glyphtrove.com/velmorina-nf.font.  The ''Labradoodles'' font is called Worstveld Sling Extra and is available freely at http://www.typebasketzone.com/KorvandelHookExtra.php.

Requirements
Must have
• Our logo
1. Home page
2. Labradoodle F.A.Q.
3. Our doodles
4. Availability
5. Adoption Process
6. Contact us
Link/badge icon for Health Guarantee
Nice to have
• Color and font to match the logo.

An area to add pictures
Should not have
• Rainbows
Rainbow colors

```html
<!DOCTYPE html>
<html lang="en">
<head>
<meta charset="utf-8">
<title>Meadow Gate Labradoodles — Our Doodles</title>
<link rel="stylesheet" href="https://fonts.googleapis.com/css2?family=Cinzel:wght@400;700&family=Open+Sans:wght@400;600&display=swap">
<style>
  :root {
    --pink: #e597a6;
    --pink-dark: #d57a8c;
    --pink-pale: #f8e3e6;
    --white: #ffffff;
    --brown: #5b3a2b;
    --brown-soft: #8a6656;
    --gray: #9a9a9a;
    --gray-light: #e6e6e6;
    --beige: #f3e8e2;
    --photo-1: #7a4b3a;
    --photo-2: #d9cbb8;
  }
  * { box-sizing: border-box; margin: 0; padding: 0; }
  html, body { width: 833px; height: 1200px; overflow: hidden; }
  body {
    position: relative;
    background: var(--pink-pale);
    font-family: "Open Sans", Arial, sans-serif;
    color: var(--brown);
  }

  /* header */
  .topbar {
    position: absolute; left: 0; top: 0; width: 833px; height: 40px;
    background: var(--pink);
  }
  .main-nav {
    position: absolute; right: 40px; top: 0; height: 40px;
    display: flex; align-items: center; gap: 26px;
  }
  .main-nav a {
    font-family: "Cinzel", Georgia, serif; font-size: 13px; font-weight: 700;
    color: var(--white); text-decoration: none;
  }
  .brand {
    position: absolute; left: 48px; top: 52px;
    display: flex; align-items: center; gap: 12px;
  }
  .brand-dot { width: 62px; height: 62px; border-radius: 50%; background: var(--brown); }
  .brand-name {
    font-family: "Cinzel", Georgia, serif; font-size: 20px; font-weight: 700;
    color: var(--brown);
  }

  /* content panel */
  .content {
    position: absolute; left: 33px; top: 150px; width: 772px; height: 785px;
    background: var(--white);
  }
  .intro { position: absolute; left: 22px; top: 52px; width: 335px; }
  .intro h1 {
    font-family: "Cinzel", Georgia, serif; font-weight: 400;
    font-size: 34px; color: var(--pink-dark); margin-bottom: 14px;
  }
  .intro p {
    font-size: 9.6px; line-height: 14.6px; color: var(--pink-dark);
    margin-bottom: 14px; text-align: justify;
  }

  .sort {
    position: absolute; left: 377px; top: 34px;
    font-size: 12px; color: var(--brown);
  }
  .sort strong { font-weight: 600; }

  .doodle-grid {
    position: absolute; left: 377px; top: 72px; width: 363px;
    display: grid; grid-template-columns: 175px 175px; column-gap: 13px; row-gap: 18px;
  }
  .doodle-card { text-align: center; }
  .doodle-photo { height: 150px; }
  .photo-a { background: linear-gradient(160deg, var(--photo-1), #a66e52); }
  .photo-b { background: linear-gradient(160deg, var(--photo-2), #efe5d8); }
  .placeholder {
    height: 150px; background: var(--gray-light);
    display: flex; align-items: center; justify-content: center;
  }
  .placeholder.short { height: 75px; }
  .doodle-name {
    font-family: "Cinzel", Georgia, serif; font-size: 15px;
    color: var(--brown); margin-top: 6px;
  }
  .doodle-meta { font-size: 8px; color: var(--gray); margin-top: 1px; }

  .scroll-track {
    position: absolute; left: 752px; top: 72px; width: 4px; height: 690px;
    background: var(--gray-light); border-radius: 2px;
  }
  .scroll-thumb {
    position: absolute; left: 0; top: 0; width: 4px; height: 170px;
    background: var(--gray); border-radius: 2px;
  }

  /* footer */
  .footer {
    position: absolute; left: 0; top: 935px; width: 833px; height: 245px;
    background: var(--beige);
  }
  .footer-nav { position: absolute; left: 55px; top: 14px; list-style: none; }
  .footer-nav li {
    font-family: "Cinzel", Georgia, serif; font-size: 17px; line-height: 28px;
    color: var(--brown);
  }
  .follow {
    position: absolute; left: 55px; top: 196px; width: 150px; height: 24px;
    background: var(--pink); border-radius: 4px;
    color: var(--white); font-size: 11px; font-weight: 600;
    display: flex; align-items: center; justify-content: center;
  }
  .contact { position: absolute; left: 305px; top: 14px; width: 255px; }
  .contact h2 {
    font-family: "Cinzel", Georgia, serif; font-weight: 400; font-size: 17px;
    color: var(--brown); margin-bottom: 6px;
  }
  .field-label { display: block; font-size: 10px; color: var(--brown); }
  .field {
    display: block; width: 255px; height: 20px; margin: 2px 0 10px;
    background: var(--white); border: 1px solid #dccbc2;
  }
  .field.area { height: 66px; }
  .submit {
    display: block; margin-left: auto; width: 64px; height: 22px;
    background: var(--pink); color: var(--white); border: 0; border-radius: 3px;
    font-family: "Open Sans", Arial, sans-serif; font-size: 11px;
  }
  .guarantee-badge { position: absolute; left: 640px; top: 45px; }

  .bottombar {
    position: absolute; left: 0; top: 1180px; width: 833px; height: 20px;
    background: var(--pink);
    display: flex; align-items: center; justify-content: center;
    font-size: 8px; color: var(--white);
  }
</style>
</head>
<body>
  <header class="topbar">
    <nav class="main-nav">
      <a href="#">Home</a><a href="#">Availability</a><a href="#">Adoption</a>
      <a href="#">Our Doodles</a><a href="#">Contact</a><a href="#">F.A.Q.</a>
    </nav>
  </header>

  <div class="brand">
    <span class="brand-dot"></span>
    <span class="brand-name">Meadow Gate Labradoodles</span>
  </div>

  <main class="content">
    <section class="intro">
      <h1>Our Doodles</h1>
      <p>Every Meadow Gate doodle is raised in our home near Charleston, surrounded by family, gentle noise and plenty of daily handling. We believe early care shapes a calm, confident companion, so our puppies meet children, visitors, other pets and the ordinary sounds of a busy household long before they leave for their new families. Our parents are chosen for sound health, soft low shedding coats and kind, steady temperaments. Each one is health tested, lives as a beloved pet and enjoys long walks, swims and lazy afternoons on the porch. When a litter arrives we keep in close touch with waiting families, sharing photos and news every week as the puppies grow. Before going home, every puppy receives a full veterinary exam, age appropriate vaccines, a microchip and a starter bag of food. We also send a soft blanket that smells of mom and littermates to ease the first nights. Our support does not end at pickup; we are always glad to answer questions about training, grooming and everyday care for the life of your doodle.</p>
      <p>Labradoodles are affectionate, clever and eager to please, which makes them wonderful family dogs and devoted companions. Our breeding program focuses on multigenerational lines that produce consistent coats, friendly personalities and dependable sizes ranging from miniature to standard. We pair each puppy with a family based on lifestyle and home rather than order of deposit, so every match feels right for both dog and people. Puppies begin early neurological stimulation at three days old and start crate, leash and potty training before they go home. We welcome visits by appointment so you can meet our dogs, see where puppies are raised and ask anything on your mind. Browse the doodles above to learn about our parents and upcoming litters, then read through our adoption process to reserve your place. If you have questions, please reach out through the contact form below and we will reply within a day or two.</p>
    </section>

    <div class="sort">Sort By &nbsp;<strong>Brown • White • Black</strong></div>

    <section class="doodle-grid">
      <article class="doodle-card">
        <div class="doodle-photo photo-a" role="img" aria-label="Photo of a brown labradoodle"></div>
        <div class="doodle-name">Doodle 1</div>
        <div class="doodle-meta">category • details • keywords • here</div>
      </article>
      <article class="doodle-card">
        <div class="doodle-photo photo-b" role="img" aria-label="Photo of a cream labradoodle"></div>
        <div class="doodle-name">Doodle 2</div>
        <div class="doodle-meta">category • details • keywords • here</div>
      </article>

      <article class="doodle-card">
        <div class="placeholder"><svg width="56" height="56" viewBox="0 0 56 56"><g fill="#f2b6c1"><ellipse cx="28" cy="38" rx="13" ry="11"/><ellipse cx="13" cy="24" rx="5" ry="7"/><ellipse cx="23" cy="15" rx="5" ry="7"/><ellipse cx="33" cy="15" rx="5" ry="7"/><ellipse cx="43" cy="24" rx="5" ry="7"/></g></svg></div>
        <div class="doodle-name">Future Doodle</div>
        <div class="doodle-meta">category • details • keywords • here</div>
      </article>
      <article class="doodle-card">
        <div class="placeholder"><svg width="56" height="56" viewBox="0 0 56 56"><g fill="#f2b6c1"><ellipse cx="28" cy="38" rx="13" ry="11"/><ellipse cx="13" cy="24" rx="5" ry="7"/><ellipse cx="23" cy="15" rx="5" ry="7"/><ellipse cx="33" cy="15" rx="5" ry="7"/><ellipse cx="43" cy="24" rx="5" ry="7"/></g></svg></div>
        <div class="doodle-name">Future Doodle</div>
        <div class="doodle-meta">category • details • keywords • here</div>
      </article>

      <article class="doodle-card">
        <div class="placeholder"><svg width="56" height="56" viewBox="0 0 56 56"><g fill="#f2b6c1"><ellipse cx="28" cy="38" rx="13" ry="11"/><ellipse cx="13" cy="24" rx="5" ry="7"/><ellipse cx="23" cy="15" rx="5" ry="7"/><ellipse cx="33" cy="15" rx="5" ry="7"/><ellipse cx="43" cy="24" rx="5" ry="7"/></g></svg></div>
        <div class="doodle-name">Future Doodle</div>
        <div class="doodle-meta">category • details • keywords • here</div>
      </article>
      <article class="doodle-card">
        <div class="placeholder"><svg width="56" height="56" viewBox="0 0 56 56"><g fill="#f2b6c1"><ellipse cx="28" cy="38" rx="13" ry="11"/><ellipse cx="13" cy="24" rx="5" ry="7"/><ellipse cx="23" cy="15" rx="5" ry="7"/><ellipse cx="33" cy="15" rx="5" ry="7"/><ellipse cx="43" cy="24" rx="5" ry="7"/></g></svg></div>
        <div class="doodle-name">Future Doodle</div>
        <div class="doodle-meta">category • details • keywords • here</div>
      </article>

      <div class="placeholder short"></div>
      <div class="placeholder short"></div>
    </section>

    <div class="scroll-track"><div class="scroll-thumb"></div></div>
  </main>

  <footer class="footer">
    <ul class="footer-nav">
      <li>Home</li><li>Availability</li><li>Adoption</li>
      <li>Our Doodles</li><li>Contact Us</li><li>FAQ</li>
    </ul>
    <div class="follow">Follow us</div>

    <form class="contact">
      <h2>Contact Us</h2>
      <label class="field-label">Name</label><span class="field"></span>
      <label class="field-label">Email</label><span class="field"></span>
      <span class="field area"></span>
      <button class="submit" type="button">Submit</button>
    </form>

    <svg class="guarantee-badge" width="165" height="165" viewBox="0 0 165 165" role="img" aria-label="Health guarantee badge">
      <circle cx="82.5" cy="82.5" r="80" fill="#d8d2d2"/>
      <circle cx="82.5" cy="82.5" r="62" fill="#f1eded" stroke="#e597a6" stroke-width="6"/>
      <circle cx="82.5" cy="82.5" r="40" fill="#e597a6"/>
    </svg>
  </footer>

  <div class="bottombar">© 2014 Meadow Gate Labradoodles. All rights reserved.</div>
</body>
</html>
```